Brightwave Reach - Business Card

We need a business card for a Social Media Marketing company that specializes in online marketing for small businesses in Canada using common Social Media platforms such as Pixlora, Chatterly, Blinkpost & Quibber.

I have uploaded a copy of our logo which I would like utilized in the business card. We would like the business card to be modern yet classy design.

Our website is www.brightwavereach.ca

Industry/Entity Type

Marketing

Contact Information for Business Card

Email: info@brightwavereach.ca
Website: www.brightwavereach.ca
Telephone: 604-555-0193

Colors

Designer to choose colors to be used in the design.

Requirements
Must have
• Social Media icons on reverse
• Please add some designs with color.

```html
<!DOCTYPE html>
<html lang="en">
<head>
<meta charset="utf-8">
<title>Brightwave Reach – Business Card</title>
<link rel="stylesheet" href="https://fonts.googleapis.com/css2?family=Roboto+Condensed:wght@700&family=Roboto:wght@400;500&display=swap">
<style>
  :root {
    --stage: #2b2b2c;
    --card-dark-start: #363b3e;
    --card-dark-end: #5d6366;
    --card-light: #f2f2f1;
    --ink: #3b3b3b;
    --ink-soft: #a3a3a3;
    --rule: #8c8c8c;
    --on-dark: #f4f4f4;
  }
  * { margin: 0; padding: 0; box-sizing: border-box; }
  html, body { width: 1200px; height: 900px; overflow: hidden; background: var(--stage); }
  .stage {
    width: 1200px; height: 900px;
    display: flex; flex-direction: column; align-items: center; justify-content: center; gap: 36px;
  }
  .card { width: 620px; height: 354px; position: relative; }
  .card--back {
    background: linear-gradient(135deg, var(--card-dark-start), var(--card-dark-end));
    display: flex; flex-direction: column; align-items: center; justify-content: center; gap: 40px;
  }
  .brand { display: flex; align-items: center; gap: 14px; }
  .brand__mark { width: 22px; height: 22px; border: 3px solid var(--on-dark); }
  .brand__name {
    font-family: "Roboto Condensed", sans-serif; font-weight: 700;
    font-size: 40px; letter-spacing: 1px; text-transform: uppercase; color: var(--on-dark);
  }
  .social { display: flex; gap: 14px; list-style: none; }
  .social__item {
    font-family: "Roboto", sans-serif; font-size: 13px; font-weight: 500; color: var(--on-dark);
    border: 1.5px solid var(--on-dark); border-radius: 14px; padding: 4px 12px;
  }
  .card--front {
    background: var(--card-light);
    display: flex; align-items: center; justify-content: center;
  }
  .identity { text-align: right; padding-right: 28px; }
  .identity__name {
    font-family: "Roboto Condensed", sans-serif; font-weight: 700;
    font-size: 34px; color: var(--ink); letter-spacing: 0.5px; line-height: 1;
  }
  .identity__title {
    font-family: "Roboto Condensed", sans-serif; font-weight: 700;
    font-size: 15px; color: var(--ink-soft); letter-spacing: 0.5px; margin-top: 6px;
  }
  .divider { width: 1px; height: 86px; background: var(--rule); }
  .contact { list-style: none; padding-left: 28px; }
  .contact__item {
    display: flex; align-items: center; gap: 10px;
    font-family: "Roboto", sans-serif; font-size: 16px; color: var(--ink); line-height: 24px;
  }
  .contact__icon { width: 14px; height: 14px; fill: var(--ink); flex: none; }
</style>
</head>
<body>
<main class="stage">
  <section class="card card--back">
    <div class="brand">
      <span class="brand__mark"></span>
      <span class="brand__name">Brightwave Reach</span>
    </div>
    <ul class="social">
      <li class="social__item">Chatterly</li>
      <li class="social__item">Pixlora</li>
      <li class="social__item">Quibber</li>
    </ul>
  </section>

  <section class="card card--front">
    <div class="identity">
      <h1 class="identity__name">DANIEL HART</h1>
      <p class="identity__title">CEO/FOUNDER</p>
    </div>
    <div class="divider"></div>
    <ul class="contact">
      <li class="contact__item">
        <svg class="contact__icon" viewBox="0 0 24 24"><path d="M6.6 10.8a15 15 0 0 0 6.6 6.6l2.2-2.2c.3-.3.7-.4 1-.2 1.1.4 2.3.6 3.6.6.6 0 1 .4 1 1V20c0 .6-.4 1-1 1A17 17 0 0 1 3 4c0-.6.4-1 1-1h3.5c.6 0 1 .4 1 1 0 1.3.2 2.5.6 3.6.1.3 0 .7-.2 1z"/></svg>
        604-555-0193
      </li>
      <li class="contact__item">
        <svg class="contact__icon" viewBox="0 0 24 24"><path d="M2 5h20v14H2z" fill="none" stroke="#3b3b3b" stroke-width="2"/><path d="M2 5l10 8 10-8" fill="none" stroke="#3b3b3b" stroke-width="2"/></svg>
        info@brightwavereach.ca
      </li>
      <li class="contact__item">
        <svg class="contact__icon" viewBox="0 0 24 24"><circle cx="12" cy="12" r="10" fill="none" stroke="#3b3b3b" stroke-width="2"/><path d="M2 12h20M12 2c3 3 3 17 0 20M12 2c-3 3-3 17 0 20" fill="none" stroke="#3b3b3b" stroke-width="1.6"/></svg>
        www.brightwavereach.ca
      </li>
    </ul>
  </section>
</main>
</body>
</html>
```